Create a Big Data Website that is professional but has a creative flare to it.

I am after a modern business design for a company in the Big Data space however it still needs to have a wow value and something stand out from other corporate websites.
My competitors websites are to give you and idea of content:
www.tarnvilla.com
www.pluvoria.com
www.meridu4.com.au
www.quornaby.com
I have uploaded my company Logo so you can use that to make sure it matches your theme.

Target Market(s)

Banks, Insurance Companies, Government, Gas and Energy Companies and Food Manufacturing.

Industry/Entity Type

Consulting

Coding

Number of Pages Required

5+ page

Colors

Designer to choose colors to be used in the design.

Requirements
Must have
• Images, Diagrams around Big Data. Usage of information or graphs from sources like Velsham are fine to use.
Nice to have
• Interactive design use mouse overs, change in text, highlighting information for clear focus.
Should not have
• Cluttered Pages of Informaiton

```html
<!DOCTYPE html>
<html lang="en">
<head>
<meta charset="utf-8">
<title>Keystrata Consulting</title>
<link href="https://fonts.googleapis.com/css2?family=Raleway:wght@400;500;600;700&display=swap" rel="stylesheet">
<style>
:root{
  --brand:#1a8fd0;
  --brand-light:#0a97d9;
  --navy:#15407a;
  --ink:#333a44;
  --muted:#5d6570;
  --sand:#f6efe5;
  --footer:#262626;
  --white:#ffffff;
}
*{margin:0;padding:0;box-sizing:border-box}
html,body{width:1200px;height:2497px;overflow:hidden}
body{font-family:'Raleway',sans-serif;color:var(--ink);background:var(--white);position:relative}
a{color:inherit}
.abs{position:absolute}

/* header */
.site-header{position:absolute;left:98px;top:0;width:1002px;height:102px;background:var(--white);border-bottom:4px solid var(--brand);z-index:5;display:flex;align-items:center;padding:0 16px}
.brand{display:flex;align-items:center;gap:10px}
.brand-mark{width:34px;height:34px;background:var(--navy)}
.brand-name{font-weight:700;font-size:22px;color:var(--navy);letter-spacing:.2px}
.main-nav{margin-left:auto;display:flex;gap:36px;font-size:13px;color:var(--ink);align-items:center}
.main-nav .active{color:var(--brand)}
.lang{width:18px;height:12px;background:#c8d2e6;display:inline-block}

/* hero */
.hero{position:absolute;left:0;top:0;width:1200px;height:588px;background:linear-gradient(180deg,#dfeaf6 0%,#9fbedf 35%,#5f86b8 70%,#2c4a73 100%)}
.hero-title{position:absolute;left:96px;top:242px;font-size:52px;font-weight:600;color:var(--white);letter-spacing:1px;text-shadow:0 2px 6px rgba(0,0,0,.25)}
.hero-sub{position:absolute;left:98px;top:312px;font-size:18px;color:var(--white)}
.hero-arrow{position:absolute;top:274px;width:38px;height:38px;border-radius:50%;background:rgba(255,255,255,.35)}

/* section headings */
.section-title{position:absolute;left:0;width:1200px;text-align:center;font-size:22px;font-weight:500;color:var(--brand);letter-spacing:.5px}
.rule{position:absolute;left:486px;width:228px;height:1px;background:#d4d8dd}
.rule::after{content:"";position:absolute;left:104px;top:-1px;width:20px;height:3px;background:var(--brand)}
.lead{position:absolute;left:200px;width:800px;text-align:center;font-size:12.5px;line-height:25px;color:var(--muted)}

/* services */
.service{position:absolute;width:230px;text-align:center}
.service svg{display:block;margin:0 auto}
.service h3{font-size:15px;font-weight:500;color:var(--ink);margin-top:20px;letter-spacing:.4px}
.service p{font-size:12px;line-height:21px;color:var(--muted);margin-top:8px}
.service a{display:inline-block;font-size:10.5px;color:var(--brand);margin-top:8px;text-decoration:underline}

/* big data band */
.band{position:absolute;left:0;top:1067px;width:1200px;height:449px;background:var(--sand)}
.band-art{position:absolute;left:116px;top:0;width:425px;height:449px;background:radial-gradient(circle at 50% 50%,#e7d3bd 0%,#f1e4d4 55%,var(--sand) 80%)}
.band-copy{position:absolute;left:591px;top:60px;width:480px}
.band-copy h2{font-size:20px;font-weight:500;color:var(--brand);letter-spacing:.4px}
.band-copy p{font-size:12px;line-height:25px;color:var(--ink);margin-top:22px}
.band-copy a{display:inline-block;margin-top:22px;font-size:12px;font-weight:600;color:var(--navy);text-decoration:underline}

/* solution cards */
.card{position:absolute;top:1674px;width:233px;height:333px}
.card-photo{height:170px}
.card-body{height:163px;position:relative;text-align:center;color:var(--white);padding:46px 14px 0}
.card.light .card-body{background:var(--brand-light)}
.card.dark .card-body{background:var(--navy)}
.card-badge{position:absolute;left:96px;top:-20px;width:40px;height:40px;border-radius:50%;display:flex;align-items:center;justify-content:center}
.card.light .card-badge{background:var(--brand-light)}
.card.dark .card-badge{background:var(--navy)}
.card h3{font-size:16px;font-weight:500}
.card p{font-size:11.5px;line-height:22px;margin-top:8px;color:#e6f1fb}

/* testimonials */
.quote{position:absolute;top:2236px;width:420px}
.avatar{position:absolute;left:0;top:0;width:110px;height:110px;border-radius:50%}
.quote-text{position:absolute;left:138px;top:18px;width:260px}
.quote-text h4{font-size:10.5px;font-weight:600;color:var(--brand);letter-spacing:.4px}
.quote-text time{display:block;font-size:10.5px;font-style:italic;color:var(--navy);margin-top:8px}
.quote-text p{font-size:11.5px;line-height:22px;color:var(--muted);margin-top:8px}
.chev{position:absolute;top:2266px;font-size:30px;color:#c4c8cd}

/* footer */
.site-footer{position:absolute;left:0;top:2403px;width:1200px;height:94px;background:var(--footer);color:#e8e8e8}
.foot-nav{position:absolute;left:100px;top:22px;font-size:11px;letter-spacing:.3px;display:flex;gap:14px}
.foot-nav span.sep{color:#999}
.copy{position:absolute;left:100px;top:56px;font-size:9px;color:#bdbdbd}
.copy a{color:#4aa8e2}
.social{position:absolute;left:925px;top:32px;display:flex;gap:10px}
.social span{width:28px;height:28px;border-radius:50%;background:#8a8a8a;display:block}
.page-tag{position:absolute;left:1166px;top:40px;font-size:11px;color:#fff}
</style>
</head>
<body>

<section class="hero" role="img" aria-label="Businessman facing a city skyline overlaid with a glowing digital network map">
  <h1 class="hero-title">KEYSTRATA CONSULTING</h1>
  <p class="hero-sub">At vero eos et accusamus et iusto odio dignissimos</p>
  <span class="hero-arrow" style="left:30px"></span>
  <span class="hero-arrow" style="left:1132px"></span>
</section>

<header class="site-header">
  <div class="brand"><span class="brand-mark"></span><span class="brand-name">keystrata consulting</span></div>
  <nav class="main-nav">
    <span class="active">Home</span><span>About</span><span>Solutions</span><span>Clients</span><span>Partners</span><span>News</span><span>Careers</span>
    <svg width="14" height="14" viewBox="0 0 14 14"><circle cx="6" cy="6" r="4.5" fill="none" stroke="#15407a" stroke-width="2"/><line x1="9.3" y1="9.3" x2="13" y2="13" stroke="#15407a" stroke-width="2"/></svg>
    <span class="lang"></span>
  </nav>
</header>

<h2 class="section-title" style="top:634px">WELCOME TO OUR COMPANY</h2>
<div class="rule" style="top:686px"></div>
<p class="lead" style="top:710px">At vero eos et accusamus et iusto odio dignissimos ducimus qui blanditiis praesentium voluptatum deleniti atque corrupti quos dolores et quas molestias excepturi sint occaecati cupiditate non provident.</p>

<div class="service" style="left:90px;top:812px">
  <svg width="84" height="92" viewBox="0 0 84 92"><polygon points="42,3 80,24 80,68 42,89 4,68 4,24" fill="none" stroke="#15407a" stroke-width="3"/><polygon points="42,9 75,27 75,65 42,83 9,65 9,27" fill="none" stroke="#15407a" stroke-width="1"/><ellipse cx="42" cy="36" rx="11" ry="4" fill="#15407a"/><path d="M31 39v6c0 2 5 4 11 4s11-2 11-4v-6c0 2-5 4-11 4s-11-2-11-4zm0 9v6c0 2 5 4 11 4s11-2 11-4v-6c0 2-5 4-11 4s-11-2-11-4z" fill="#15407a"/></svg>
  <h3>DATA WAREHOUSING</h3>
  <p>On the other hand, we denounce with beguiled and demoralized</p>
  <a>READ MORE</a>
</div>
<div class="service" style="left:353px;top:812px">
  <svg width="84" height="92" viewBox="0 0 84 92"><polygon points="42,3 80,24 80,68 42,89 4,68 4,24" fill="none" stroke="#1a8fd0" stroke-width="2"/><rect x="32" y="33" width="14" height="18" fill="none" stroke="#1a8fd0" stroke-width="2"/><rect x="38" y="40" width="14" height="18" fill="#fff" stroke="#1a8fd0" stroke-width="2"/></svg>
  <h3>BUSINESS INTELLIGENCE</h3>
  <p>On the other hand, we denounce with beguiled and demoralized</p>
  <a>READ MORE</a>
</div>
<div class="service" style="left:616px;top:812px">
  <svg width="84" height="92" viewBox="0 0 84 92"><polygon points="42,3 80,24 80,68 42,89 4,68 4,24" fill="none" stroke="#1a8fd0" stroke-width="2"/><line x1="33" y1="57" x2="49" y2="40" stroke="#1a8fd0" stroke-width="3"/><path d="M50 33l1.5 3.5 3.5 1.5-3.5 1.5-1.5 3.5-1.5-3.5-3.5-1.5 3.5-1.5z" fill="#1a8fd0"/></svg>
  <h3>ADVANCED ANALYTICS</h3>
  <p>On the other hand, we denounce with beguiled and demoralized</p>
  <a>READ MORE</a>
</div>
<div class="service" style="left:879px;top:812px">
  <svg width="84" height="92" viewBox="0 0 84 92"><polygon points="42,3 80,24 80,68 42,89 4,68 4,24" fill="none" stroke="#1a8fd0" stroke-width="2"/><rect x="31" y="34" width="22" height="22" fill="none" stroke="#1a8fd0" stroke-width="2"/><rect x="35" y="44" width="3" height="9" fill="#1a8fd0"/><rect x="40" y="39" width="3" height="14" fill="#1a8fd0"/><rect x="45" y="42" width="3" height="11" fill="#1a8fd0"/></svg>
  <h3>BIG DATA</h3>
  <p>On the other hand, we denounce with beguiled and demoralized</p>
  <a>READ MORE</a>
</div>

<section class="band">
  <div class="band-art" role="img" aria-label="Illustration of hands holding a tablet with charts, surrounded by data and analytics icons"></div>
  <div class="band-copy">
    <h2>BIG DATA</h2>
    <p>At vero eos et accusamus et iusto odio dignissimos ducimus qui blanditiis praesentium voluptatum deleniti atque corrupti quos dolores et quas molestias excepturi sint occaecati cupiditate non provident.</p>
    <p>Sed ut perspiciatis unde omnis iste natus error sit voluptatem accusantium doloremque laudantium, totam rem aperiam, eaque ipsa quae ab illo inventore veritatis et quasi architecto beatae vitae dicta sunt explicabo. Nemo enim ipsam voluptatem quia voluptas sit aspernatur aut odit aut fugit, sed quia consequuntur magni dolores eos qui ratione voluptatem sequi nesciunt. Neque porro quisquam est, qui dolorem ipsum quia dolor sit amet, consectetur.</p>
    <a>READ MORE</a>
  </div>
</section>

<h2 class="section-title" style="top:1566px">BIG DATA ANALYTICS SOLUTIONS</h2>
<div class="rule" style="top:1619px"></div>

<article class="card light" style="left:98px">
  <div class="card-photo" role="img" aria-label="Team reviewing charts on a desktop monitor" style="background:linear-gradient(135deg,#c9b79f,#7a6a5c)"></div>
  <div class="card-body"><span class="card-badge"><svg width="16" height="12" viewBox="0 0 16 12"><path d="M1 6h13M9 1l5 5-5 5" fill="none" stroke="#fff" stroke-width="2"/></svg></span><h3>Commercial Strategy</h3><p>At vero eos et accusamus et iusto odio dignissimos ducimus qui blan praesen tium voluptatum...</p></div>
</article>
<article class="card dark" style="left:354px">
  <div class="card-photo" role="img" aria-label="Hand touching a network of cloud and data icons" style="background:linear-gradient(135deg,#8fa3b8,#2f4157)"></div>
  <div class="card-body"><span class="card-badge"><svg width="16" height="12" viewBox="0 0 16 12"><path d="M1 6h13M9 1l5 5-5 5" fill="none" stroke="#fff" stroke-width="2"/></svg></span><h3>Big Data Platform</h3><p>At vero eos et accusamus et iusto odio dignissimos ducimus qui blan praesen tium voluptatum...</p></div>
</article>
<article class="card light" style="left:611px">
  <div class="card-photo" role="img" aria-label="Hand holding a glowing light bulb over a notebook" style="background:linear-gradient(135deg,#e6d7c2,#6d6155)"></div>
  <div class="card-body"><span class="card-badge"><svg width="16" height="12" viewBox="0 0 16 12"><path d="M1 6h13M9 1l5 5-5 5" fill="none" stroke="#fff" stroke-width="2"/></svg></span><h3>Insights</h3><p>At vero eos et accusamus et iusto odio dignissimos ducimus qui blan praesen tium voluptatum...</p></div>
</article>
<article class="card dark" style="left:867px">
  <div class="card-photo" role="img" aria-label="Hand over glowing financial data visuals" style="background:linear-gradient(135deg,#2a3f6b,#c86a3a)"></div>
  <div class="card-body"><span class="card-badge"><svg width="16" height="12" viewBox="0 0 16 12"><path d="M1 6h13M9 1l5 5-5 5" fill="none" stroke="#fff" stroke-width="2"/></svg></span><h3>Data Science</h3><p>At vero eos et accusamus et iusto odio dignissimos ducimus qui blan praesen tium voluptatum...</p></div>
</article>

<h2 class="section-title" style="top:2056px">TESTIMONIALS</h2>
<div class="rule" style="top:2102px"></div>
<p class="lead" style="top:2121px;left:160px;width:880px">At vero eos et accusamus et iusto odio dignissimos ducimus qui blanditiis praesentium voluptatum deleniti atque corrupti quos dolores et quas molestias excepturi sint occaecati cupiditate non provident.</p>
<svg class="abs" style="left:340px;top:2190px" width="520" height="14" viewBox="0 0 520 14"><line x1="0" y1="7" x2="253" y2="7" stroke="#d4d8dd"/><circle cx="260" cy="7" r="4" fill="none" stroke="#c4c8cd"/><line x1="267" y1="7" x2="520" y2="7" stroke="#d4d8dd"/></svg>

<span class="chev" style="left:150px">&#8249;</span>
<span class="chev" style="left:1034px">&#8250;</span>
<div class="quote" style="left:198px">
  <div class="avatar" role="img" aria-label="Portrait of a client" style="background:#d9cfc6"></div>
  <div class="quote-text"><h4>NEMO ENIM IPSAM</h4><time>Posted on 29 Sep 2017</time><p>At vero eos et accusamus et iusto odio dignissimos ducimus qui praesentium.</p></div>
</div>
<div class="quote" style="left:627px">
  <div class="avatar" role="img" aria-label="Portrait of a client" style="background:#cfd3d8"></div>
  <div class="quote-text"><h4>NEMO ENIM IPSAM</h4><time>Posted on 29 Sep 2017</time><p>At vero eos et accusamus et iusto odio dignissimos ducimus qui praesentium.</p></div>
</div>

<footer class="site-footer">
  <nav class="foot-nav"><span>HOME</span><span class="sep">/</span><span>ABOUT</span><span class="sep">/</span><span>SOLUTIONS</span><span class="sep">/</span><span>CLIENTS</span><span class="sep">/</span><span>PARTNERS</span><span class="sep">/</span><span>NEWS</span><span class="sep">/</span><span>CAREERS</span></nav>
  <p class="copy">© COPYRIGHT 2017. <a>KEYSTRATA CONSULTING</a>. ALL RIGHTS RESERVED.</p>
  <div class="social"><span></span><span></span><span></span><span></span><span></span></div>
  <span class="page-tag">C1</span>
</footer>

</body>
</html>
```